Specialised investor in e-mobility and energy wants business card design

We need a business card design that fits our existing corporate design. <The look and feel must be 'sharp'/'clean', dynamic, communicate momentum, professionalism etc (as one would imagine from a firm in the financial sector). We like the idea of a reverse-side of the card that includes the logo, and the name and contact details on the other. We expect the deliverable to be whatever format might be required to be able to get cards printed directly by a service such as kelmo press. Our website is www.zub.capital

```html
<!DOCTYPE html>
<html lang="en">
<head>
<meta charset="utf-8">
<title>Zub Capital – Business Card</title>
<link href="https://fonts.googleapis.com/css2?family=Montserrat:wght@400;500;700&display=swap" rel="stylesheet">
<style>
  :root {
    --forest: #334f24;
    --forest-deep: #26401b;
    --leaf: #86b24a;
    --ink: #2b2b2b;
    --paper: #ffffff;
    --backdrop: #e4e4e2;
  }
  * { margin: 0; padding: 0; box-sizing: border-box; }
  html, body {
    width: 1200px; height: 801px; overflow: hidden;
    background: var(--backdrop);
    font-family: "Montserrat", sans-serif;
  }
  .sheet {
    position: relative; width: 1200px; height: 801px;
    display: flex; align-items: center; justify-content: center; gap: 40px;
  }
  .card {
    position: relative; width: 540px; height: 309px; overflow: hidden;
    box-shadow: 0 6px 18px rgba(0,0,0,.18);
  }
  /* Front: contact side */
  .card--front { background: var(--paper); border-bottom: 3px solid var(--leaf); }
  .card__swoosh { position: absolute; inset: 0; width: 100%; height: 100%; }
  .brand {
    position: absolute; left: 40px; top: 108px;
    font-weight: 500; font-size: 34px; letter-spacing: .5px;
    color: var(--forest);
  }
  .divider {
    position: absolute; left: 262px; top: 36px; width: 1px; height: 166px;
    background: var(--leaf);
  }
  .contact { position: absolute; left: 284px; top: 36px; color: var(--ink); }
  .contact__name {
    font-weight: 700; font-size: 17px; letter-spacing: .8px;
    color: var(--leaf); text-transform: uppercase;
  }
  .contact__role { font-size: 12.5px; margin-top: 2px; }
  .contact__list { list-style: none; margin-top: 14px; font-size: 12px; line-height: 18px; }
  .contact__list li { display: flex; align-items: center; gap: 7px; }
  .contact__list svg { width: 10px; height: 10px; fill: var(--leaf); flex: none; }
  .contact__company { margin-top: 14px; font-size: 12.5px; color: var(--leaf); }
  .contact__city { font-size: 12.5px; }

  /* Back: brand side */
  .card--back {
    background: var(--forest); border-bottom: 3px solid var(--leaf);
    display: flex; align-items: center; justify-content: center;
  }
  .brand--large { position: static; font-size: 58px; font-weight: 500; color: var(--paper); }
</style>
</head>
<body>
<main class="sheet">
  <section class="card card--front" aria-label="Business card front">
    <svg class="card__swoosh" viewBox="0 0 540 309" preserveAspectRatio="none" aria-hidden="true">
      <path d="M190,309 C270,250 400,228 540,222 L540,309 Z" fill="var(--forest)"/>
      <path d="M160,309 C250,236 400,208 540,200 L540,212 C400,220 262,244 176,309 Z" fill="var(--leaf)"/>
      <path d="M215,309 C290,262 400,242 540,236" fill="none" stroke="var(--paper)" stroke-width="2.5"/>
    </svg>
    <div class="brand">Zub Capital</div>
    <div class="divider"></div>
    <div class="contact">
      <div class="contact__name">Lena Marwood</div>
      <div class="contact__role">Managing Director</div>
      <ul class="contact__list">
        <li><svg viewBox="0 0 10 10"><path d="M1,2 Q5,-1 9,2 L8,4 L6,3 L6,4 L4,4 L4,3 L2,4 Z M2,5 H8 V9 H2 Z"/></svg>+41 79 000 4418</li>
        <li><svg viewBox="0 0 10 10"><path d="M0,2 H10 V8 H0 Z M0,2 L5,6 L10,2" /></svg>lena@zub.capital</li>
        <li><svg viewBox="0 0 10 10"><circle cx="5" cy="5" r="5"/></svg>www.zub.capital</li>
      </ul>
      <div class="contact__company">Zub Capital S.A.</div>
      <div class="contact__city">Geneva, Switzerland</div>
    </div>
  </section>

  <section class="card card--back" aria-label="Business card back">
    <div class="brand brand--large">Zub Capital</div>
  </section>
</main>
</body>
</html>
```